Business card design needed

My business is in Matchmaking. My objective is to find the most compatible partner for my clients....basically I'm in the love and happiness industry bringing two people together for a lasting loving relationship.

I envision the design to be something with 2 people who are in love looking happy or even a silhouette.....I don't really know, I'm open to ideas.....maybe no picture at all, but I want it to be classy :-)

I do have a logo which I will upload. You can also go to my website to give you an idea on the colours and the design if that helps, however the website is not finished yet, it should be up by today or tomorrow. If the website has a heart with swirls on the upper left hand corner, that is the old website, please ignore that one. The one that will be up shortly has a picture frame on the home page with my logo that will be in the file I will upload on this page.

Target Market(s)

There are three categories: Over 45, Asian and Western and same sex, but would be able to afford to hire a matchmaker

Contact Information for Business Card

The Tidewell Bureau
Helping You Find The "One"
Mavis Ellery
Matchmaker
0492 517 264
info@tidewellbureau.com.au
www.tidewellbureau.com.au

```html
<!DOCTYPE html>
<html lang="en">
<head>
<meta charset="utf-8">
<title>The Tidewell Bureau – Business Card</title>
<link rel="stylesheet" href="https://fonts.googleapis.com/css2?family=Open+Sans:wght@400;600;700&display=swap">
<style>
  :root {
    --backdrop: #e9e6e4;
    --card-white: #f6f5f1;
    --plum-deep: #5b3b57;
    --plum-band: #9c7490;
    --plum-band-light: #b894ad;
    --lavender-strip: #dcc7d6;
    --photo-dark: #6f6a68;
    --photo-light: #e2dedb;
    --mint: #8fc2b2;
    --text-light: #ffffff;
  }
  * { box-sizing: border-box; margin: 0; padding: 0; }
  html, body {
    width: 1200px; height: 1000px; overflow: hidden;
    background: var(--backdrop);
    font-family: "Open Sans", Arial, sans-serif;
  }
  .business-card {
    position: absolute; left: 100px; top: 214px;
    width: 1000px; height: 572px;
    background: var(--card-white);
    box-shadow: 0 6px 24px rgba(0,0,0,0.12);
    overflow: hidden;
  }
  .accent-strip {
    position: absolute; left: 470px; top: 0; right: 0; height: 24px;
    background: var(--lavender-strip);
  }
  .hands-photo {
    position: absolute; left: 560px; top: 24px; right: 0; height: 236px;
    background: radial-gradient(ellipse at 50% 55%, var(--photo-dark) 0%, #a9a4a1 45%, var(--photo-light) 80%);
  }
  .contact-panel {
    position: absolute; left: 470px; top: 260px; right: 0; bottom: 0;
    background: linear-gradient(135deg, var(--plum-band) 0%, var(--plum-band-light) 100%);
  }
  .person-name {
    position: absolute; right: 36px; top: 14px;
    color: var(--text-light); font-weight: 700; font-size: 42px; line-height: 1;
    text-align: right;
  }
  .person-role {
    position: absolute; right: 36px; top: 60px;
    color: var(--text-light); font-weight: 600; font-size: 20px;
  }
  .contact-list {
    position: absolute; left: 40px; top: 140px;
    list-style: none; color: var(--text-light);
    font-weight: 600; font-size: 24px; line-height: 38px;
  }
  .brand-block {
    position: absolute; left: 0; top: 170px; width: 470px;
    text-align: center;
  }
  .brand-mark {
    display: inline-block; width: 64px; height: 64px; border-radius: 50%;
    background: var(--mint); margin-bottom: 18px;
  }
  .brand-name {
    font-weight: 600; font-size: 38px; color: var(--plum-deep);
  }
  .brand-tagline {
    margin-top: 18px; font-weight: 700; font-size: 27px; color: var(--plum-deep);
  }
</style>
</head>
<body>
  <main class="business-card">
    <div class="accent-strip"></div>
    <div class="hands-photo" role="img" aria-label="Black and white photograph of two clasped hands"></div>
    <section class="contact-panel">
      <h1 class="person-name">Mavis Ellery</h1>
      <p class="person-role">Matchmaker</p>
      <ul class="contact-list">
        <li>Tel. 0492 517 264</li>
        <li>info@tidewellbureau.com.au</li>
        <li>www.tidewellbureau.com.au</li>
      </ul>
    </section>
    <div class="brand-block">
      <span class="brand-mark"></span>
      <p class="brand-name">The Tidewell Bureau</p>
      <p class="brand-tagline">Helping You Find The "One"</p>
    </div>
  </main>
</body>
</html>
```